Business cards and stationary design

We just completed the design of our new logo and we need to print new business cards and letterhead for our nonprofit. We are looking for a fresh new design that shows off our new logo. On letterhead, we must have a column on the right or left to include our Board of Directors (up to 45 names) (see attachment)

Industry/Entity Type

Non-Profit

Contact Information for Business Card

Standard business card with name, title, Company name, mailing address phone numbers, email address and website. Tagline on back "Bringing the homeless home"

Font styles to use
Sans Serif

Requirements
Must have
• include pertinent information above
• new logo
• fonts compatible with logo
• should use logo colors only
Nice to have
• tag lines

```html
<!DOCTYPE html>
<html lang="en">
<head>
<meta charset="utf-8">
<title>Northwind Shelter Network — Letterhead</title>
<link rel="stylesheet" href="https://fonts.googleapis.com/css2?family=Roboto:wght@400;500&family=Questrial&display=swap">
<style>
  :root {
    --backdrop: #e9e9e9;
    --paper-top: #f6f6f6;
    --paper-bottom: #e6e6e6;
    --ink: #3f3f3f;
    --ink-soft: #5a5a5a;
    --rule: #9a9a9a;
    --signature-tint: #d6e0ee;
  }
  * { box-sizing: border-box; margin: 0; padding: 0; }
  html, body { width: 1024px; height: 1200px; overflow: hidden; }
  body { background: var(--backdrop); position: relative; font-family: 'Roboto', Arial, sans-serif; color: var(--ink); }

  .letterhead {
    position: absolute; left: 152px; top: 96px; width: 720px; height: 1008px;
    background: linear-gradient(180deg, var(--paper-top), var(--paper-bottom));
    box-shadow: 0 2px 10px rgba(0,0,0,0.12);
  }

  .brand {
    position: absolute; left: 70px; top: 96px; width: 180px;
    display: flex; align-items: center; gap: 8px;
    font-family: 'Roboto', Arial, sans-serif; font-weight: 400; font-size: 14px;
    line-height: 17px; color: var(--ink);
  }
  .brand-mark { width: 10px; height: 10px; border-radius: 50%; background: var(--ink); flex: none; }

  .sender { position: absolute; left: 506px; top: 69px; font-style: normal; font-size: 10.5px; line-height: 12.4px; color: var(--ink-soft); }
  .sender p + p { margin-top: 5px; }

  .board { position: absolute; right: 528px; top: 240px; text-align: right; font-size: 10.5px; line-height: 14.3px; color: var(--ink-soft); }
  .board-title { font-weight: 500; color: var(--ink); margin-bottom: 14px; }
  .board-officers { margin-bottom: 13px; }
  .board-officers strong { font-weight: 500; color: var(--ink); }
  .board ul { list-style: none; }

  .column-rule { position: absolute; left: 249px; top: 240px; width: 1px; height: 614px; background: var(--rule); }

  .letter { position: absolute; left: 312px; top: 243px; width: 344px; font-family: 'Questrial', 'Century Gothic', sans-serif; color: var(--ink-soft); }
  .salutation { font-size: 18px; color: var(--ink); margin-bottom: 30px; }
  .letter-body p { font-size: 11.6px; line-height: 14.3px; letter-spacing: 0.3px; text-align: justify; hyphens: auto; margin-bottom: 18px; }
  .closing { position: absolute; left: 312px; top: 786px; font-family: 'Questrial', 'Century Gothic', sans-serif; font-size: 10.6px; color: var(--ink-soft); }
  .signature { position: absolute; left: 308px; top: 804px; width: 108px; height: 50px; border-radius: 4px; background: linear-gradient(90deg, var(--signature-tint), rgba(214,224,238,0.3)); }
</style>
</head>
<body>
  <main class="letterhead">
    <header>
      <div class="brand"><span class="brand-mark"></span><span class="brand-name">Northwind Shelter Network</span></div>
      <address class="sender">
        <p>NORTHWIND SHELTER NETWORK<br>1420 Alder Court<br>Fairbanks, Alaska 99701</p>
        <p>555 210 4187<br>mara@northwindshelter.org<br>www.northwindshelter.org</p>
      </address>
    </header>

    <aside class="board">
      <p class="board-title">Board of Directors:</p>
      <ul class="board-officers">
        <li><strong>Ralph Dunmore</strong>, Chair</li>
        <li><strong>Neil Ostrand</strong>, Vice Chair</li>
        <li><strong>Lena Whitcomb</strong>, Treasurer</li>
        <li><strong>Tara Bellamy</strong>, Secretary</li>
      </ul>
      <ul class="board-members">
        <li>Owen Pratt</li><li>Hugo Vance</li><li>Peter Lindahl</li><li>Clara Renwick</li>
        <li>Miles Carden</li><li>Reid Ashford</li><li>Nadine Corwell</li><li>Dean Morrow</li>
        <li>Gwen Tally</li><li>Marion Keasler</li><li>Priya Venkat</li><li>Ivy Marsh</li>
        <li>Wade Holloway</li><li>Colin Harrow</li><li>Jenna Castell</li><li>Brent Oakes</li>
        <li>Noel Fairbank</li><li>Rosa Delgado</li><li>Janine Pruitt</li><li>Celia Vornholt</li>
        <li>Hannah Ridley</li><li>Tessa Langford</li><li>Victor Halstead</li><li>Simon Kovalik</li>
        <li>Grant Ellery</li><li>Laurel Winfield</li><li>Derek Novotny</li><li>Mina Rosales</li>
        <li>Paula Brightwell</li><li>Elise Harker</li><li>Vanessa Quill</li><li>Farida Nazarova</li>
        <li>Bridget Conley</li><li>Rory Tennant</li><li>Grace Liang</li><li>Marco Bellini</li>
      </ul>
    </aside>

    <div class="column-rule"></div>

    <article class="letter">
      <p class="salutation">Dear Mr. Carter,</p>
      <div class="letter-body">
        <p>Lorem ipsum dolor sit amet, consectetur adipiscing elit. Donec orci purus, luctus vitae dignissim eu, iaculis sed purus. Vivamus faucibus, ipsum nec aliquet viverra, leo mauris condimentum ligula, sit amet sagittis enim ligula quis arcu. Nam egestas tortor id nisi porttitor mattis. In tortor ante, ultricies in suscipit a, tempus non massa. Vivamus et auctor mi. Fusce vel massa nulla. Phasellus nec eros mauris, et scelerisque orci.</p>
        <p>Donec malesuada orci vitae nulla accumsan porta a id massa. Quisque accumsan iaculis magna sit amet fringilla. Maecenas consequat, magna eget tincidunt semper, odio nibh rutrum mi, id feugiat ante nisi eu risus. Vestibulum nunc orci, rhoncus a placerat in, ultricies in mi. Cras mattis varius eros, vel fringilla nisi suscipit eget. Quisque scelerisque sagittis nulla at porttitor.</p>
        <p>Sed id augue vitae urna euismod commodo aliquet a quam. Pellentesque arcu velit, cursus et malesuada ut, consequat et diam. Nullam erat sem, rhoncus id ullamcorper vitae, rhoncus et arcu. In ultricies ultricies nulla, ut rutrum nisi iaculis at. Donec eu magna a metus ornare faucibus. Fusce aliquet faucibus ultricies. Morbi semper, est id tincidunt gravida, sem arcu adipiscing lacus, ac bibendum nulla leo eu purus. Quisque nec diam sed risus consectetur a ccumsan quis quis nibh. Vestibulum id purus lorem.</p>
        <p>It is a long established fact that a reader will be distracted by the readable content of a page when looking at its layout. The point of using Lorem Ipsum is that it has a more-or-less normal distribution of letters, as opposed to using 'Content here, content here', making it look like readable English. Many desktop publishing packages</p>
      </div>
    </article>

    <p class="closing">Sincerely,</p>
    <div class="signature" role="img" aria-label="Handwritten signature of Mara Lindqvist in blue ink"></div>
  </main>
</body>
</html>
```